Lawn sign for construction company

Would like this to be a very clean and high end design for luxury homes. We need a yard sign designed that includes the company logo, website, phone number and major service offerings (residential and commercial renovations and maintenance)
The company website is brackwellbuilders.com all other contact info is in the attachments
Target Market(s)
Luxury home owners and business owners
Industry/Entity Type
Construction/Home Improvement
Font styles to use
Other font styles liked:
- See company logo and other graphics included for title text fonts. All other fonts can be standard sans serif.
Colors
0054AA
0677BA
7BADD7
CADEEF
E8F1F8
Requirements
Must have
- Clean, easy to read design, would like 2 sided sign. A main sign side and back side which states “free estimates, and includes the website and phone number. Must also match the color scheme of the provided logo and other company images. Dark Navy blue primary color, gray secondary color, and orange as an accent color.
Nice to have
- 2nd sign side very simple design
Should not have
- Too many graphics limit to 1-3 colors

```html
<!DOCTYPE html>
<html lang="en">
<head>
<meta charset="utf-8">
<title>Brackwell Builders – Yard Sign, Two Sides</title>
<link rel="stylesheet" href="https://fonts.googleapis.com/css2?family=Montserrat:wght@400;500;700;800&display=swap">
<style>
  :root {
    --stage: #757374;
    --gray-dark: #cacaca;
    --gray-light: #dcdcdc;
    --navy: #020a5e;
    --orange: #e8760c;
    --white: #ffffff;
    --text-gray: #6c6c6c;
    --text-dark: #2b2b2b;
  }
  html, body {
    margin: 0;
    padding: 0;
    width: 1200px;
    height: 1200px;
    overflow: hidden;
    background: var(--stage);
  }
  .canvas {
    position: relative;
    width: 1200px;
    height: 1200px;
    font-family: "Montserrat", sans-serif;
  }
  .sign {
    position: absolute;
    left: 225px;
    width: 750px;
    height: 500px;
    display: block;
  }
  .sign--front { top: 72px; }
  .sign--back { top: 627px; }

  .fill-gray-dark { fill: var(--gray-dark); }
  .fill-gray-light { fill: var(--gray-light); }
  .fill-navy { fill: var(--navy); }
  .fill-orange { fill: var(--orange); }
  .frame-line { fill: none; stroke: var(--navy); stroke-width: 1.5; }
  .rule-line { stroke: var(--navy); stroke-width: 1.2; }
  .dash-line { stroke: var(--text-dark); stroke-width: 1.2; }

  .brand-name {
    font-family: "Montserrat", sans-serif;
    font-weight: 800;
    fill: var(--orange);
    letter-spacing: 1px;
  }
  .headline {
    font-weight: 700;
    fill: var(--white);
    font-size: 28px;
    letter-spacing: 3px;
  }
  .phone-front {
    font-weight: 800;
    fill: var(--white);
    font-size: 70px;
  }
  .website {
    font-weight: 500;
    fill: var(--orange);
    font-size: 27px;
    letter-spacing: 3.5px;
  }
  .contact-label {
    font-weight: 400;
    fill: var(--text-dark);
    font-size: 24px;
  }
  .phone-back {
    font-weight: 700;
    fill: var(--navy);
    font-size: 58px;
  }
  .services {
    font-weight: 700;
    fill: var(--text-gray);
    font-size: 23px;
    letter-spacing: 0.5px;
  }
  .services .divider { fill: var(--orange); }
</style>
</head>
<body>
<main class="canvas">

  <!-- Front face -->
  <svg class="sign sign--front" viewBox="0 0 750 500" aria-label="Front of yard sign">
    <rect class="fill-gray-light" width="750" height="500"/>
    <polygon class="fill-gray-dark" points="0,0 750,0 750,10 0,490 0,0"/>
    <rect class="fill-gray-light" x="17" y="14" width="718" height="473" opacity="0"/>
    <rect class="frame-line" x="17.5" y="14.5" width="717" height="472"/>

    <!-- band -->
    <polygon class="fill-navy" points="17,233 375,335 735,233 735,487 17,487"/>
    <polygon class="fill-orange" points="30,240 375,335 720,240 735,240 375,343 17,240"/>
    <polygon class="fill-navy" points="17,240 375,343 735,240 735,487 17,487"/>

    <!-- company name -->
    <text class="brand-name" x="375" y="168" text-anchor="middle" font-size="40">BRACKWELL BUILDERS</text>

    <text class="headline" x="383" y="370" text-anchor="middle">CALL FOR FREE ESTIMATES</text>

    <!-- phone icon -->
    <g class="phone-icon" transform="translate(80,386)">
      <path class="fill-orange" d="M6 4 C9 2 12 3 13 6 L16 14 C17 17 15 19 13 20 L11 21 C13 28 19 34 26 36 L27 34 C28 32 31 30 34 31 L41 34 C44 35 45 38 43 41 L40 45 C37 48 32 49 27 47 C15 42 5 32 1 20 C-1 14 1 8 6 4 Z"/>
      <path d="M28 10 A12 12 0 0 1 38 20" fill="none" stroke="var(--orange)" stroke-width="2.5"/>
      <path d="M29 3 A19 19 0 0 1 45 19" fill="none" stroke="var(--orange)" stroke-width="2.5"/>
      <path d="M27 17 A6 6 0 0 1 31 21" fill="none" stroke="var(--orange)" stroke-width="2.5"/>
    </g>
    <text class="phone-front" x="418" y="440" text-anchor="middle">800-555-0142</text>

    <text class="website" x="380" y="478" text-anchor="middle">www.brackwellbuilders.com</text>
  </svg>

  <!-- Back face -->
  <svg class="sign sign--back" viewBox="0 0 750 500" aria-label="Back of yard sign">
    <rect class="fill-gray-light" width="750" height="500"/>
    <polygon class="fill-gray-dark" points="0,0 750,0 0,500"/>

    <!-- company name -->
    <text class="brand-name" x="375" y="190" text-anchor="middle" font-size="48">BRACKWELL BUILDERS</text>

    <line class="dash-line" x1="240" y1="345" x2="268" y2="345"/>
    <text class="contact-label" x="375" y="354" text-anchor="middle">CONTACT US ON</text>
    <line class="dash-line" x1="482" y1="345" x2="510" y2="345"/>

    <text class="phone-back" x="375" y="409" text-anchor="middle">800.555.0142</text>

    <line class="rule-line" x1="88" y1="419" x2="662" y2="419"/>

    <text class="services" x="375" y="448" text-anchor="middle">RESIDENTIAL RENOVATIONS <tspan class="divider">■</tspan> COMMERCIAL</text>
    <text class="services" x="375" y="474" text-anchor="middle">RENOVATIONS <tspan class="divider">■</tspan> MAINTENANCE</text>
  </svg>

</main>
</body>
</html>
```